Business Card Design

Looking for business card designs for a new business. there will be two cards of the same design (both lots of information below in contact info). We would like the logo diagonally across the card with the information split above and below the logo similar to sketch. happy to look at similar alternatives
Please use same colours as in logo design

Industry/Entity Type

Business

Contact Information for Business Card

Dwight Halloran
mob - 0491 738 204
ph - 02 6148 3920
fax - 02 6148 3975
email - dwight@kestrelbeams.com.au
14 Larkmoor Road, Taminda NSW 2340

Colin Marchetti
mob - 0438 912 557
ph - 02 6148 3920
fax - 02 6148 3975
email - colin@kestrelbeams.com.au

```html
<!DOCTYPE html>
<html lang="en">
<head>
<meta charset="utf-8">
<title>Kestrel Beams – Business Card</title>
<link href="https://fonts.googleapis.com/css2?family=PT+Sans:wght@400;700&display=swap" rel="stylesheet">
<style>
  :root {
    --backdrop: #4b4b4b;
    --card-white: #ffffff;
    --teal: #0d807f;
    --ink: #070708;
    --text-light: #ffffff;
  }
  html, body {
    margin: 0;
    padding: 0;
    width: 1200px;
    height: 999px;
    overflow: hidden;
    background: var(--backdrop);
    font-family: "PT Sans", "Myriad Pro", Arial, sans-serif;
  }
  .card {
    position: absolute;
    left: 75px;
    top: 199px;
    width: 1050px;
    height: 599px;
    background: var(--card-white);
    overflow: hidden;
  }
  .brand {
    position: absolute;
    top: 0;
    left: 0;
    width: 100%;
    height: 248px;
    display: flex;
    align-items: center;
    justify-content: center;
    gap: 18px;
  }
  .brand-mark {
    width: 46px;
    height: 46px;
    background: var(--teal);
  }
  .brand-name {
    font-weight: 700;
    font-size: 74px;
    color: var(--ink);
    letter-spacing: 0.5px;
  }
  .rule {
    position: absolute;
    top: 248px;
    left: 0;
    width: 100%;
    height: 8px;
    background: var(--ink);
  }
  .contact-panel {
    position: absolute;
    top: 256px;
    left: 0;
    width: 100%;
    height: 272px;
    background: var(--teal);
    color: var(--text-light);
  }
  .person-name {
    position: absolute;
    left: 50px;
    top: 29px;
    margin: 0;
    font-size: 41px;
    font-weight: 700;
    line-height: 1;
  }
  .contact-list {
    position: absolute;
    left: 48px;
    top: 96px;
    margin: 0;
    padding: 0;
    list-style: none;
  }
  .contact-list li {
    display: flex;
    align-items: center;
    height: 41px;
    font-size: 31px;
  }
  .contact-list svg {
    width: 30px;
    height: 30px;
    flex: none;
  }
  .divider {
    margin: 0 12px 0 14px;
    font-size: 28px;
  }
  .address-bar {
    position: absolute;
    top: 528px;
    left: 0;
    width: 100%;
    height: 71px;
    background: var(--ink);
    color: var(--text-light);
    font-size: 30px;
    text-align: center;
    line-height: 50px;
  }
</style>
</head>
<body>
  <div class="card">
    <div class="brand">
      <span class="brand-mark"></span>
      <span class="brand-name">Kestrel Beams</span>
    </div>
    <div class="rule"></div>
    <section class="contact-panel">
      <h1 class="person-name">Dwight Halloran</h1>
      <ul class="contact-list">
        <li>
          <svg viewBox="0 0 30 30" aria-hidden="true"><rect x="2" y="2" width="26" height="26" rx="4" fill="#fff"/><rect x="9" y="5" width="12" height="20" rx="2" fill="none" stroke="#0d807f" stroke-width="2"/><line x1="10" y1="7" x2="20" y2="22" stroke="#0d807f" stroke-width="2"/></svg>
          <span class="divider">|</span><span>0491 738 204</span>
        </li>
        <li>
          <svg viewBox="0 0 30 30" aria-hidden="true"><rect x="2" y="2" width="26" height="26" rx="4" fill="#fff"/><path d="M10 7 L13 7 L14 11 L12 13 Q14 18 18 19 L20 17 L23 18 L23 21 Q15 23 10 15 Q8 11 10 7 Z" fill="#0d807f"/></svg>
          <span class="divider">|</span><span>02 6148 3920</span>
        </li>
        <li>
          <svg viewBox="0 0 30 30" aria-hidden="true"><rect x="8" y="2" width="13" height="10" fill="#fff"/><rect x="3" y="13" width="24" height="9" fill="#fff"/><rect x="3" y="24" width="24" height="4" fill="#fff"/></svg>
          <span class="divider">|</span><span>02 6148 3975</span>
        </li>
        <li>
          <svg viewBox="0 0 30 30" aria-hidden="true"><path d="M2 12 L15 4 L28 12 L28 27 L2 27 Z" fill="#fff"/><path d="M5 13 L15 20 L25 13" fill="none" stroke="#0d807f" stroke-width="2"/></svg>
          <span class="divider">|</span><span>dwight@kestrelbeams.com.au</span>
        </li>
      </ul>
    </section>
    <footer class="address-bar">14 Larkmoor Road, Corrowell NSW 2917 Colin</footer>
  </div>
</body>
</html>
```